Business Card Design Project

We are not a new company, but renamed to "Vantorin Kitchens" last year. We specialize in modern high-end cabinetry imports. We would like to communicate a sense of quality and cutting edge technology. Ideally the design would incorporate our logo colors, silver, red and preferably a black, matte background. Though we are open to suggestions.
Logo is attached.
Edit: I have attached rough drafts of the previous cards, this way you will have all necessary content that needs to go on the cards.
Updates
Project Deadline Extended
Reason: We have received a lot of great designs, but due to the sheer number we couldn't respond to all. We will extend the deadline for another 7 days to finalize and provide feedback to designers.
Thank you for your hard work!
Industry/Entity Type
Business
Look and feel
Each slider illustrates characteristics of the customer's brand and the style your logo design should communicate.

```html
<!DOCTYPE html>
<html lang="en">
<head>
<meta charset="utf-8">
<title>Vantorin Kitchens – Business Cards</title>
<link rel="stylesheet" href="https://fonts.googleapis.com/css2?family=Open+Sans:wght@400;600&display=swap">
<style>
  :root {
    --backdrop: #4a2c1b;
    --card-top: #1d1d1f;
    --card-bottom: #0b0b0c;
    --card-edge: #2a2a2c;
    --silver: #c9cbce;
    --silver-dim: #8d8f93;
    --band: #050505;
    --band-line: #5a5b5e;
    --white: #f2f2f2;
    --red: #d01620;
  }
  * { margin: 0; padding: 0; box-sizing: border-box; }
  html, body { width: 1200px; height: 750px; overflow: hidden; }
  body {
    background: var(--backdrop);
    font-family: "Open Sans", Arial, sans-serif;
    position: relative;
  }
  .card {
    position: absolute;
    left: 316px;
    width: 592px;
    border-radius: 22px;
    background: radial-gradient(ellipse at 50% 30%, var(--card-top) 0%, var(--card-bottom) 85%);
    border: 1px solid var(--card-edge);
    box-shadow: 0 4px 14px rgba(0,0,0,0.45);
    overflow: hidden;
  }
  .card--front { top: 21px; height: 325px; }
  .card--back { top: 366px; height: 361px; }

  .brand {
    position: absolute;
    left: 0; right: 0;
    display: flex;
    align-items: center;
    justify-content: center;
    gap: 16px;
    color: var(--silver);
    font-weight: 600;
    letter-spacing: 0.06em;
    text-transform: uppercase;
  }
  .brand__square {
    background: var(--red);
    flex: none;
  }
  .card--front .brand { top: 140px; font-size: 40px; }
  .card--front .brand__square { width: 26px; height: 26px; }
  .card--back .brand { top: 130px; font-size: 32px; }
  .card--back .brand__square { width: 20px; height: 20px; }

  .contact-band {
    position: absolute;
    left: 0; right: 0;
    top: 232px;
    height: 82px;
    background: var(--band);
    border-top: 1px solid var(--band-line);
    border-bottom: 1px solid var(--band-line);
  }
  .contact-list {
    position: absolute;
    left: 56px;
    top: 6px;
    list-style: none;
    font-size: 13px;
    line-height: 15px;
    color: var(--silver-dim);
  }
  .person {
    position: absolute;
    right: 58px;
    top: 20px;
    text-align: right;
    color: var(--white);
  }
  .person__name { font-size: 20px; font-weight: 600; line-height: 24px; }
  .person__role { font-size: 8px; font-weight: 600; line-height: 10px; }
</style>
</head>
<body>
  <section class="card card--front">
    <div class="brand"><span class="brand__square"></span>Vantorin Kitchens</div>
  </section>

  <section class="card card--back">
    <div class="brand"><span class="brand__square"></span>Vantorin Kitchens</div>
    <div class="contact-band">
      <ul class="contact-list">
        <li>Adress:</li>
        <li>Phone:</li>
        <li>Cell:</li>
        <li>Fax:</li>
        <li>Email:</li>
      </ul>
      <div class="person">
        <div class="person__name">Marcus Hallin</div>
        <div class="person__role">Director</div>
      </div>
    </div>
  </section>
</body>
</html>
```